Brightfield Ventures Inc. Letterhead

Creation of attractive and eye catching letterhead for a business start-up for the construction industry. Letterhead must relate to construction, but avoid standard hammer and tools in the design.

I forgot to add some details, sorry about that. Some pertinent info: Ph: 916-555-0187 brightfieldventures.example 448 Willowmere Ave, Ste 210 Folsom, CA 95999 info@brightfieldventures.example not sure if slogan should be in there" “Connecting construction professionals to create a purpose driven industry.” must be able to be used in word. Thanks!

```html
<!DOCTYPE html>
<html lang="en">
<head>
<meta charset="utf-8">
<title>Brightfield Ventures Inc. Letterhead</title>
<link href="https://fonts.googleapis.com/css2?family=Open+Sans:wght@400;600;700&family=Arimo:wght@700&display=swap" rel="stylesheet">
<style>
  :root {
    --backdrop: #e3e4e5;
    --paper: #ffffff;
    --brand-red: #c0141b;
    --brand-navy: #23305f;
    --ink: #3a3a3a;
    --ink-soft: #555555;
    --rule: #8a8fa8;
  }
  * { box-sizing: border-box; margin: 0; padding: 0; }
  html, body { width: 1200px; height: 945px; overflow: hidden; }
  body {
    background: var(--backdrop);
    font-family: "Open Sans", Arial, sans-serif;
    color: var(--ink);
  }
  .letterhead {
    position: absolute;
    left: 280px;
    top: 20px;
    width: 640px;
    height: 905px;
    background: var(--paper);
    box-shadow: 0 4px 18px rgba(0,0,0,0.12);
    overflow: hidden;
  }
  .header-bands, .footer-band { position: absolute; left: 0; width: 640px; display: block; }
  .header-bands { top: 0; height: 60px; }
  .footer-band { bottom: 0; height: 20px; }

  .brand {
    position: absolute;
    left: 34px;
    top: 70px;
    display: flex;
    align-items: center;
    gap: 8px;
  }
  .brand-mark { width: 14px; height: 14px; background: var(--brand-red); }
  .brand-name {
    font-size: 17px;
    font-weight: 700;
    color: var(--brand-navy);
    letter-spacing: 0.3px;
  }

  .company-info {
    position: absolute;
    left: 312px;
    top: 62px;
    font-size: 9px;
    font-style: normal;
    line-height: 1.35;
    color: var(--ink-soft);
  }
  .company-name { color: var(--brand-red); font-weight: 700; font-size: 9.5px; }
  .info-divider {
    position: absolute;
    left: 456px;
    top: 62px;
    width: 1px;
    height: 40px;
    background: var(--rule);
  }
  .contact-list {
    position: absolute;
    left: 466px;
    top: 58px;
    list-style: none;
    font-size: 8.5px;
    line-height: 1.45;
    color: var(--ink-soft);
  }
  .contact-list li { display: flex; align-items: center; gap: 5px; white-space: nowrap; }
  .contact-list svg { width: 8px; height: 8px; fill: var(--brand-red); flex: none; }

  .letter-body {
    position: absolute;
    left: 110px;
    top: 200px;
    width: 470px;
  }
  .salutation {
    font-family: "Arimo", Arial, sans-serif;
    font-weight: 700;
    font-size: 13px;
    color: var(--ink);
    margin-bottom: 14px;
  }
  .letter-body p {
    font-size: 11.5px;
    line-height: 1.42;
    text-align: justify;
    margin-bottom: 18px;
    padding-left: 14px;
    color: var(--ink);
  }
  .signature {
    margin-top: 22px;
    margin-left: 30px;
    width: 140px;
    height: 44px;
    background: linear-gradient(90deg, #f1f1f1, #e6e6e6);
    border-radius: 4px;
  }
</style>
</head>
<body>
  <article class="letterhead">
    <svg class="header-bands" viewBox="0 0 640 60" preserveAspectRatio="none" aria-hidden="true">
      <path d="M0,20 Q340,14 560,0 L640,0 L640,40 Q380,18 0,30 Z" fill="var(--brand-red)"/>
      <path d="M0,31 Q380,19 640,42 L640,45 Q380,24 0,36 Z" fill="var(--brand-navy)"/>
    </svg>

    <div class="brand">
      <span class="brand-mark"></span>
      <span class="brand-name">Brightfield Ventures</span>
    </div>

    <address class="company-info">
      <div class="company-name">Brightfield Ventures Inc.</div>
      <div>448 Willowmere Ave, Ste 210,</div>
      <div>Folsom, CA 95999</div>
    </address>
    <span class="info-divider"></span>
    <ul class="contact-list">
      <li><svg viewBox="0 0 10 10"><path d="M2,0 L4,2.5 L3,4 Q4.5,6 6,7 L7.5,6 L10,8 L8.5,10 Q3,9 0,1.5 Z"/></svg>916-555-0187</li>
      <li><svg viewBox="0 0 10 10"><path d="M0,2 L10,2 L10,8 L0,8 Z M0.5,2.5 L5,5.5 L9.5,2.5" stroke="#fff" stroke-width="0.8"/></svg>info@brightfieldventures.example</li>
      <li><svg viewBox="0 0 10 10"><circle cx="5" cy="5" r="4.5"/><circle cx="5" cy="5" r="2" fill="#fff"/></svg>brightfieldventures.example</li>
    </ul>

    <section class="letter-body">
      <h2 class="salutation">Dear Mr. Harlan,</h2>
      <p>Lorem Ipsum is simply dummy text of the printing and typesetting industry. Lorem Ipsum has been the industry's standard dummy text ever since the 1500s, when an unknown printer took a galley of type and scrambled it to make a type specimen book. It has survived not only five centuries, but also the leap into electronic typesetting, remaining essentially unchanged.</p>
      <p>The standard chunk of Lorem Ipsum used since the 1500s is reproduced below for those interested. Sections 1.10.32 and 1.10.33 from "de Rebus Fabricandis" by Aurelio Vance are also reproduced in their exact original form, accompanied by English versions from the 1914 translation by H.Morrow</p>
      <p>Lorem Ipsum is simply dummy text of the printing and typesetting industry. Lorem Ipsum has been the industry's standard dummy text ever since the 1500s, when an unknown printer took a galley of type and scrambled it to make a type specimen book. It has survived not only five centuries, but also the leap into electronic typesetting, remaining essentially unchanged. It was popularised in the</p>
      <p>The standard chunk of Lorem Ipsum used since the 1500s is reproduced below for those interested. Sections 1.10.32 and 1.10.33 from "de Rebus Fabricandis" by Aurelio Vance are also reproduced in their exact original form, accompanied by English versions from the 1914 translation by H.Morrow</p>
      <div class="signature" role="img" aria-label="Handwritten signature of the sender"></div>
    </section>

    <svg class="footer-band" viewBox="0 0 640 20" preserveAspectRatio="none" aria-hidden="true">
      <path d="M0,12 L640,4 L640,20 L0,20 Z" fill="var(--brand-red)"/>
    </svg>
  </article>
</body>
</html>
```